Harborline Auto LLC

Car Dealer Customer Service
Address: 2874 Cresthaven Road, Shelbyville, TN 37162
web: www.harborlineautoxq.net
email: harborlineautoxq@mailnest.example
Phone: (931) 555-0148
Phone: (629) 555-0173

```html
<!DOCTYPE html>
<html lang="en">
<head>
<meta charset="utf-8">
<title>Harborline Auto — Business Card</title>
<link href="https://fonts.googleapis.com/css2?family=Poppins:wght@400;500;700&family=Roboto+Condensed:wght@700&display=swap" rel="stylesheet">
<style>
  :root {
    --page-bg: #e7e4e0;
    --card-bg: #f3f2f0;
    --card-edge: #d9d7d3;
    --brand-blue: #1f7ea6;
    --brand-gold: #e0a83a;
    --ink: #1f1f1f;
    --band-text: #fbf3e4;
  }
  * { margin: 0; padding: 0; box-sizing: border-box; }
  html, body {
    width: 1200px; height: 1054px; overflow: hidden;
    background: var(--page-bg);
  }
  .canvas {
    position: relative; width: 1200px; height: 1054px;
    display: flex; align-items: center; justify-content: center;
  }
  .card {
    position: relative; width: 900px; height: 541px;
    background: var(--card-bg);
    border: 1px solid var(--card-edge);
    border-radius: 18px;
    box-shadow: 0 12px 40px rgba(0,0,0,0.12);
    overflow: hidden;
    font-family: "Poppins", sans-serif;
    color: var(--ink);
  }
  .brand-mark {
    position: absolute; left: 50%; top: 70px;
    width: 170px; height: 170px; margin-left: -85px;
    border-radius: 50%;
    background: var(--brand-blue);
    opacity: 0.9;
  }
  .brand-name {
    position: absolute; left: 0; right: 0; top: 258px;
    text-align: center;
    font-family: "Poppins", sans-serif;
    font-weight: 700; font-size: 46px; letter-spacing: 1px;
    color: var(--brand-blue);
  }
  .tagline {
    position: absolute; left: 0; right: 0; top: 338px;
    text-align: center; font-size: 21px; font-weight: 400;
  }
  .phone-band {
    position: absolute; left: 0; right: 0; top: 376px; height: 65px;
    background: var(--brand-blue);
    display: flex; align-items: center; justify-content: center; gap: 34px;
  }
  .phone {
    display: flex; align-items: center; gap: 14px;
    font-family: "Roboto Condensed", sans-serif;
    font-weight: 700; font-size: 44px;
    color: var(--band-text);
  }
  .phone-icon { width: 42px; height: 42px; flex: none; }
  .address {
    position: absolute; left: 0; right: 0; top: 452px;
    text-align: center; font-size: 21px;
  }
  .web-line {
    position: absolute; left: 0; right: 0; top: 484px;
    text-align: center; font-size: 21px;
  }
  .web-line .divider { margin: 0 10px; }
</style>
</head>
<body>
<main class="canvas">
  <section class="card">
    <div class="brand-mark" aria-hidden="true"></div>
    <h1 class="brand-name">HARBORLINE AUTO</h1>
    <p class="tagline">Car Dealer Customer Service</p>
    <div class="phone-band">
      <span class="phone">
        <svg class="phone-icon" viewBox="0 0 42 42" aria-hidden="true">
          <circle cx="21" cy="21" r="18" fill="none" stroke="#e0a83a" stroke-width="3"/>
          <path d="M14 12.5c1-1 2.4-.9 3.1.2l1.6 2.6c.5.9.3 2-.5 2.6l-1.2.9c1 2.3 2.9 4.2 5.2 5.2l.9-1.2c.6-.8 1.7-1 2.6-.5l2.6 1.6c1.1.7 1.2 2.1.2 3.1l-1.3 1.3c-1.2 1.2-3 1.5-4.5.8-4.6-2-8.2-5.6-10.2-10.2-.7-1.5-.4-3.3.8-4.5z" fill="#e0a83a"/>
        </svg>
        931-555-0148
      </span>
      <span class="phone">
        <svg class="phone-icon" viewBox="0 0 42 42" aria-hidden="true">
          <circle cx="21" cy="21" r="18" fill="none" stroke="#e0a83a" stroke-width="3"/>
          <path d="M14 12.5c1-1 2.4-.9 3.1.2l1.6 2.6c.5.9.3 2-.5 2.6l-1.2.9c1 2.3 2.9 4.2 5.2 5.2l.9-1.2c.6-.8 1.7-1 2.6-.5l2.6 1.6c1.1.7 1.2 2.1.2 3.1l-1.3 1.3c-1.2 1.2-3 1.5-4.5.8-4.6-2-8.2-5.6-10.2-10.2-.7-1.5-.4-3.3.8-4.5z" fill="#e0a83a"/>
        </svg>
        629-555-0173
      </span>
    </div>
    <p class="address">2874 Cresthaven Road, Shelbyville, TN 37162</p>
    <p class="web-line">www.harborlineautoxq.net<span class="divider">|</span>harborlineautoxq@mailnest.example</p>
  </section>
</main>
</body>
</html>
```